TALMORK

The business want a professional looking business card. We have a scetch we will add but want the extra upgrade, and would like more suggestions for variations of our business cards.

```html
<!DOCTYPE html>
<html lang="en">
<head>
<meta charset="utf-8">
<title>TALMORK business cards</title>
<link rel="stylesheet" href="https://fonts.googleapis.com/css2?family=Gilda+Display&family=Marcellus&family=Nunito+Sans:wght@400&display=swap">
<style>
  :root {
    --backdrop: #1d1d1f;
    --card: #141415;
    --gold: #c9a770;
    --gold-soft: #d8c3a0;
    --gold-line: #a88a58;
  }
  * { margin: 0; padding: 0; box-sizing: border-box; }
  html, body {
    width: 1200px; height: 805px; overflow: hidden;
    background: var(--backdrop);
  }
  .canvas { position: relative; width: 1200px; height: 805px; }
  .card {
    position: absolute; top: 231px;
    width: 480px; height: 335px;
    background: var(--card);
  }
  .card--front { left: 101px; }
  .card--back { left: 626px; }

  .company {
    position: absolute; right: 112px; top: 38px;
    font-family: "Marcellus", serif; font-size: 21px;
    color: var(--gold); letter-spacing: 0.5px; white-space: nowrap;
  }
  .role {
    position: absolute; right: 112px; top: 71px;
    font-family: "Nunito Sans", sans-serif; font-size: 17px;
    color: var(--gold-soft);
  }
  .divider {
    position: absolute; left: 390px; top: 27px;
    width: 1.5px; height: 279px; background: var(--gold-line);
  }
  .mark-dot {
    position: absolute; left: 418px; top: 40px;
    width: 22px; height: 22px; border-radius: 50%;
    border: 1.5px solid var(--gold);
  }
  .person {
    position: absolute; left: 35px; top: 130px;
    font-family: "Gilda Display", serif; font-size: 32px;
    color: var(--gold-soft); white-space: nowrap;
  }
  .contacts { position: absolute; left: 33px; top: 215px; list-style: none; }
  .contacts li {
    display: flex; align-items: center; height: 30px;
    font-family: "Nunito Sans", sans-serif; font-size: 18px;
    color: var(--gold-soft);
  }
  .contacts svg { width: 20px; height: 20px; margin-right: 12px; flex: none; }

  .brand-ring {
    position: absolute; left: 50%; top: 92px; transform: translateX(-50%);
    width: 90px; height: 90px; border-radius: 50%;
    border: 1.5px solid #3a3530;
  }
  .brand {
    position: absolute; left: 0; right: 0; top: 215px; text-align: center;
    font-family: "Marcellus", serif; font-size: 32px;
    letter-spacing: 9px; padding-left: 9px; color: var(--gold);
  }
  .since {
    position: absolute; left: 0; right: 0; top: 259px; text-align: center;
    font-family: "Nunito Sans", sans-serif; font-size: 12px;
    letter-spacing: 4px; padding-left: 4px; color: var(--gold-line);
  }
</style>
</head>
<body>
<main class="canvas">
  <section class="card card--front" aria-label="Business card front">
    <p class="company">TALMORK VARMO</p>
    <p class="role">CEO &amp; Founder</p>
    <span class="divider"></span>
    <span class="mark-dot"></span>
    <h1 class="person">Anders Lund Varmo</h1>
    <ul class="contacts">
      <li>
        <svg viewBox="0 0 20 20" fill="none" stroke="#c9a770" stroke-width="1.5"><rect x="6" y="2" width="8" height="16" rx="1.5"/><line x1="9" y1="15.5" x2="11" y2="15.5"/></svg>
        004791234567
      </li>
      <li>
        <svg viewBox="0 0 20 20" fill="#c9a770"><path d="M3 5h14v10H3z"/><path d="M3 5l7 6 7-6" fill="none" stroke="#141415" stroke-width="1.3"/></svg>
        talmork.llc@mailbox.com
      </li>
      <li>
        <svg viewBox="0 0 20 20" fill="none" stroke="#c9a770" stroke-width="1.4"><circle cx="10" cy="10" r="7"/><ellipse cx="10" cy="10" rx="3" ry="7"/><line x1="3" y1="10" x2="17" y2="10"/></svg>
        www.talmork.llc
      </li>
    </ul>
  </section>

  <section class="card card--back" aria-label="Business card back">
    <span class="brand-ring"></span>
    <p class="brand">TALMORK</p>
    <p class="since">SINCE 2026</p>
  </section>
</main>
</body>
</html>
```